U.S. Popcorn company needs business cards

We are a popcorn company that manufactures popcorn and sells it to grocery stores worldwide. Our theme is "Americana" and our logo is U.S. route 66 which is the most famous highway in the U.S.

We would like the design to be simple and to use both sides. On the back side we would like to see just the logo and website. The front would be normal details

Target Market(s)

Wholesalers, grocers and distributors

Industry/Entity Type

Manufacture

Contact Information for Business Card

Business name: Prairie Lantern Popcorn
Phone: +1 555 308 4726
Email: Dale@prairielanternpopcorn.com
website: www.prairielanternpopcorn.com
Tag Line: "POPped fresh daily"
Name: Dale Whitcombe
Title: Founder/President

Requirements
Must have
• Either this design should be fun or clean and simple. I will let you show me your thougths.
Nice to have
• Anything that ties in the real Hwy Route 66.
• Colors might need to be red, white and blue incorporated.
Should not have
• Not be too busy.

```html
<!DOCTYPE html>
<html lang="en">
<head>
<meta charset="utf-8">
<title>Prairie Lantern Popcorn – Business Cards</title>
<link rel="stylesheet" href="https://fonts.googleapis.com/css2?family=Open+Sans:ital,wght@0,400;0,600;0,700;1,600&display=swap">
<style>
  :root {
    --navy: #0f2a66;
    --red: #e3202a;
    --white: #ffffff;
    --ink: #3a3f4a;
    --rule: #c9ccd3;
    --backdrop: #e9e6e1;
  }
  * { box-sizing: border-box; margin: 0; padding: 0; }
  html, body {
    width: 1200px; height: 987px; overflow: hidden;
    background: var(--backdrop);
    font-family: "Open Sans", Arial, sans-serif;
  }
  .card {
    position: absolute; left: 293px; width: 615px; height: 351px;
    box-shadow: 0 3px 8px rgba(0,0,0,0.25);
  }
  .card-front { top: 130px; background: var(--white); overflow: hidden; }
  .card-back { top: 506px; background: var(--navy); }

  .brand-mark {
    position: absolute; left: 52px; top: 118px; width: 200px;
    color: var(--navy); font-weight: 700; font-size: 24px; line-height: 1.2;
    text-align: center;
  }
  .divider {
    position: absolute; left: 267px; top: 87px; width: 1px; height: 175px;
    background: var(--rule);
  }
  .contact-block { position: absolute; left: 297px; top: 104px; }
  .person-name { color: var(--navy); font-weight: 600; font-size: 21px; line-height: 1.2; }
  .person-title { color: var(--red); font-size: 16px; line-height: 1.3; margin-bottom: 12px; }
  .contact-list { list-style: none; }
  .contact-list li {
    display: flex; align-items: center; gap: 10px;
    color: var(--ink); font-size: 15px; line-height: 23.5px;
  }
  .contact-list svg { width: 14px; height: 14px; fill: var(--navy); flex: none; }

  .stripe { position: absolute; left: 0; bottom: 0; width: 615px; height: 17px; }

  .back-mark {
    position: absolute; left: 0; right: 0; top: 136px;
    color: var(--white); font-weight: 700; font-size: 34px; line-height: 1.2;
    text-align: center;
  }
  .tagline {
    position: absolute; left: 0; right: 0; top: 296px;
    color: var(--white); font-size: 17px; text-align: center;
    font-style: italic; font-weight: 600;
  }
  .tagline b { font-style: normal; font-weight: 700; }
</style>
</head>
<body>
  <section class="card card-front" aria-label="Card front">
    <div class="brand-mark">Prairie Lantern<br>Popcorn</div>
    <div class="divider"></div>
    <div class="contact-block">
      <p class="person-name">Dale Whitcombe</p>
      <p class="person-title">Founder/President</p>
      <ul class="contact-list">
        <li>
          <svg viewBox="0 0 24 24" aria-hidden="true"><path d="M6.6 10.8a15.1 15.1 0 0 0 6.6 6.6l2.2-2.2a1 1 0 0 1 1-.25 11.4 11.4 0 0 0 3.6.57 1 1 0 0 1 1 1V20a1 1 0 0 1-1 1A17 17 0 0 1 3 4a1 1 0 0 1 1-1h3.5a1 1 0 0 1 1 1c0 1.25.2 2.45.57 3.57a1 1 0 0 1-.25 1z"/></svg>
          +1 555 308 4726
        </li>
        <li>
          <svg viewBox="0 0 24 24" aria-hidden="true"><path d="M2 5h20v14H2z M3.5 6.5 12 13l8.5-6.5" fill="none" stroke="#0f2a66" stroke-width="2"/></svg>
          Dale@prairielanternpopcorn.com
        </li>
        <li>
          <svg viewBox="0 0 24 24" aria-hidden="true"><circle cx="12" cy="12" r="10"/><path d="M2 12h20M12 2c3 3 3 17 0 20M12 2c-3 3-3 17 0 20" fill="none" stroke="#fff" stroke-width="1.4"/></svg>
          www.prairielanternpopcorn.com
        </li>
      </ul>
    </div>
    <svg class="stripe" viewBox="0 0 615 17" preserveAspectRatio="none" aria-hidden="true">
      <polygon points="0,0 401,0 397,17 0,17" fill="var(--navy)"/>
      <polygon points="405,0 615,0 615,17 401,17" fill="var(--red)"/>
    </svg>
  </section>

  <section class="card card-back" aria-label="Card back">
    <div class="back-mark">Prairie Lantern<br>Popcorn</div>
    <p class="tagline"><b>POP</b>ped fresh daily</p>
  </section>
</body>
</html>
```